Verodex business card

Business card for sustainable investment company called "Verodex". Verodex is an exchange platform selling carbon credits between buyers and sellers. Carbon Credits are an environmental commodity for reducing global carbon emissions.

the card should obviously have our logo and the theme should be sustainability/environment mixed with a trading platform.

Contact Information for Business Card

Logo, Name, Title, Phone, Email

Colors
0054AA
0677BA
7BADD7
CADEEF
E8F1F8
0094D4
00A9DD
6FCCEA
C7EBF8
E9F6FB
00AB8E
00BBA5
67D7C9
C6EFE9
E9F9F6
59FF00
82FF00
B8FF75
E3FFCB
F4FFEA

```html
<!DOCTYPE html>
<html lang="en">
<head>
<meta charset="utf-8">
<title>Verodex Business Card</title>
<link href="https://fonts.googleapis.com/css2?family=Montserrat:wght@400;500;600;700&display=swap" rel="stylesheet">
<style>
  :root{
    --bg:#2a2b2d;
    --white:#ffffff;
    --navy:#2f4560;
    --navy-deep:#1c2f5c;
    --sky:#35bde8;
    --aqua:#62cbdc;
    --blue:#3f6fb8;
    --mid:#3a9ede;
    --text:#1f2430;
  }
  *{margin:0;padding:0;box-sizing:border-box}
  html,body{width:1200px;height:960px;overflow:hidden}
  body{background:var(--bg);font-family:"Montserrat",sans-serif;position:relative}
  .card{position:absolute;left:300px;width:600px;height:343px;border-radius:22px;overflow:hidden}
  .card--front{top:100px;background:linear-gradient(25deg,var(--aqua) 0%,var(--sky) 42%,var(--mid) 62%,var(--blue) 88%)}
  .card--back{top:517px;background:var(--white)}

  .brand{position:absolute;display:flex;align-items:center;gap:18px}
  .brand__mark{display:block;border-radius:8px}
  .brand__name{font-weight:600;letter-spacing:1px;line-height:1}
  .card--front .brand{left:0;right:0;top:140px;justify-content:center}
  .card--front .brand__mark{width:54px;height:54px;border:7px solid var(--white)}
  .card--front .brand__name{color:var(--white);font-size:58px}
  .card--back .brand{left:110px;top:44px}
  .card--back .brand__mark{width:58px;height:58px;background:linear-gradient(30deg,var(--aqua),var(--sky) 50%,var(--blue))}
  .card--back .brand__name{color:var(--navy);font-size:56px}

  .person{position:absolute;right:318px;top:130px;text-align:right}
  .person__name{font-weight:700;font-size:24px;letter-spacing:.5px;white-space:nowrap}
  .person__first{color:var(--sky)}
  .person__last{color:var(--navy)}
  .person__title{font-size:16px;color:var(--text);margin-top:4px}

  .divider{position:absolute;left:296px;top:126px;width:2px;height:74px;background:var(--sky)}

  .contacts{position:absolute;left:310px;top:124px;list-style:none}
  .contacts__item{display:flex;align-items:center;gap:9px;font-size:16px;color:var(--text);height:26px}
  .contacts__icon{width:18px;height:18px;flex:none}

  .wave{position:absolute;left:0;top:0;width:600px;height:343px}
</style>
</head>
<body>
  <section class="card card--front" aria-label="Card front">
    <div class="brand">
      <span class="brand__mark"></span>
      <span class="brand__name">VERODEX</span>
    </div>
  </section>

  <section class="card card--back" aria-label="Card back">
    <svg class="wave" viewBox="0 0 600 343" aria-hidden="true">
      <defs>
        <linearGradient id="bandFill" x1="0" y1="1" x2="1" y2="0">
          <stop offset="0" stop-color="#62cbdc"/>
          <stop offset="0.45" stop-color="#35bde8"/>
          <stop offset="1" stop-color="#3f6fb8"/>
        </linearGradient>
      </defs>
      <path d="M0,302 C150,314 260,306 360,276 C450,248 520,215 600,205 L600,343 L0,343 Z" fill="url(#bandFill)"/>
      <path d="M120,298 C240,296 310,278 380,254 C450,230 515,206 585,192" fill="none" stroke="#1c2f5c" stroke-width="4" stroke-linecap="round"/>
    </svg>

    <div class="brand">
      <span class="brand__mark"></span>
      <span class="brand__name">VERODEX</span>
    </div>

    <div class="person">
      <p class="person__name"><span class="person__first">DANIEL</span> <span class="person__last">MARSH</span></p>
      <p class="person__title">Co-Founder</p>
    </div>

    <span class="divider"></span>

    <ul class="contacts">
      <li class="contacts__item">
        <svg class="contacts__icon" viewBox="0 0 20 20" aria-hidden="true"><path d="M5 2l3 4-2 2c1 2 3 4 5 5l2-2 4 3-2 3C9 17 3 11 2 5z" fill="#3a9ede"/></svg>
        555-214-0398
      </li>
      <li class="contacts__item">
        <svg class="contacts__icon" viewBox="0 0 20 20" aria-hidden="true"><rect x="2" y="5" width="16" height="11" fill="#3a9ede"/><path d="M2 5l8 6 8-6" fill="none" stroke="#fff" stroke-width="1.5"/></svg>
        info@verodex.com
      </li>
      <li class="contacts__item">
        <svg class="contacts__icon" viewBox="0 0 20 20" aria-hidden="true"><circle cx="10" cy="10" r="8" fill="#3a9ede"/><path d="M2 10h16M10 2c-4 4-4 12 0 16M10 2c4 4 4 12 0 16" fill="none" stroke="#fff" stroke-width="1.2"/></svg>
        www.verodex.com
      </li>
    </ul>
  </section>
</body>
</html>
```